Recruitment of Trellan Staffing for the UK market

I want a website for the UK market to attract businesses and companies to come to us for Philipine labour. We want an information site that gives all information on what we do and how we can recruit Philippine labour.
This is a recruitment site for companies to contact us with their requirements for skilled workers coming from the Philipines over to the UK to work.

Target Market(s)

Uk Companies and businesses who want Philipine skilled workers

Industry/Entity Type

REcruitment

Coding

Number of Pages Required

5+ page

Font styles to use
Sans Serif

Colors
0054AA
0677BA
7BADD7
CADEEF
E8F1F8
0094D4
00A9DD
6FCCEA
C7EBF8
E9F6FB
EE7325
F08F49
F5BC92
FAE3D3
FDF4ED
EB3D1F
EC4F4E
F09395
F8D3D4
FCEDEE

Requirements
Must have
• Look professional and corperate with drop down menus for Home ,about, services,articles. training , contact us
Nice to have
• Look at Velmora recruitment- https://velmorarecruitment.example.co.uk/. This is my current site - https://www.trellanstaffing.example.com/
Should not have
• Cartoons or silly pictures , needs to be corperate looking

```html
<!DOCTYPE html>
<html lang="en">
<head>
<meta charset="utf-8">
<title>Trellan Staffing – Skilled Philippine Workers for UK Companies</title>
<link href="https://fonts.googleapis.com/css2?family=Montserrat:wght@400;500;600;700&family=Oswald:wght@500;600&display=swap" rel="stylesheet">
<style>
:root{
  --blue:#0054AA;
  --blue-mid:#0677BA;
  --blue-soft:#CADEEF;
  --orange:#EE7325;
  --red:#EB3D1F;
  --ink:#1f1f1f;
  --muted:#555;
  --grey-bg:#f3f3f3;
  --line:#d9d9d9;
  --white:#fff;
}
*{box-sizing:border-box;margin:0;padding:0}
html,body{width:1200px;height:5190px;overflow:hidden}
body{font-family:"Montserrat",sans-serif;color:var(--ink);background:var(--white);position:relative}
section,header,footer{position:absolute;left:0;width:1200px}
.btn{position:absolute;display:inline-block;background:var(--blue);color:var(--white);font-size:12px;font-weight:600;padding:11px 20px;text-decoration:none}
.btn--light{background:var(--white);color:var(--blue)}
.rule{display:block;width:44px;height:3px;background:var(--orange)}
.photo{position:absolute}
.h2{font-size:30px;font-weight:600;line-height:1.3}

/* header */
.site-header{top:0;height:82px;background:var(--white)}
.brand{position:absolute;left:162px;top:26px;display:flex;align-items:center;gap:10px;font-size:20px;font-weight:700;color:var(--blue)}
.brand__dot{width:26px;height:26px;background:var(--red)}
.nav{position:absolute;left:545px;top:32px;display:flex;gap:0}
.nav a{font-size:12.5px;font-weight:500;color:var(--ink);text-decoration:none;margin-right:42px}
.nav a.is-active{color:var(--blue);text-decoration:underline}

/* hero */
.hero{top:82px;height:563px}
.hero__bg{inset:0;background:linear-gradient(90deg,#6b6a58 0%,#8e8a6e 35%,#b6a58a 60%,#d8883c 80%,#8fa2b8 100%)}
.hero__title{position:absolute;left:163px;top:172px;font-family:"Oswald",sans-serif;font-weight:600;font-size:45px;line-height:1.17;color:var(--white);text-transform:uppercase}
.hero .btn{left:163px;top:345px}

/* about */
.about{top:645px;height:573px;background:var(--grey-bg)}
.about__blob{position:absolute;left:460px;top:352px;width:100px;height:100px;border-radius:50%;background:#cfcfcf}
.about__photo{left:160px;top:90px;width:395px;height:395px;border-radius:50%;background:linear-gradient(135deg,#e9eef3,#9aa9b8 60%,#4c5e7a)}
.about__title{position:absolute;left:633px;top:152px}
.about__text{position:absolute;left:633px;top:258px;width:400px;font-size:11.5px;line-height:23px;color:var(--ink)}
.about .btn{left:633px;top:393px}

/* working together */
.together{top:1218px;height:540px}
.together__title{position:absolute;left:162px;top:132px}
.together .rule{position:absolute;left:162px;top:178px}
.together__text{position:absolute;left:162px;top:202px;width:360px;font-size:15px;line-height:34px}
.together__text a{color:var(--red);font-weight:700}
.together .btn{left:162px;top:346px}
.together__map{left:630px;top:57px;width:380px;height:385px;background:radial-gradient(ellipse at 55% 45%,#d8ecf6,#ffffff 70%)}

/* services cards */
.help{top:1758px;height:544px;background:var(--grey-bg)}
.card{position:absolute;top:90px;width:260px;height:288px;background:var(--white);text-align:center;box-shadow:0 2px 8px rgba(0,0,0,.06)}
.card svg{margin-top:34px}
.card h3{font-size:15.5px;font-weight:600;margin-top:24px}
.card p{font-size:11px;line-height:23px;color:var(--ink);margin:14px auto 0;width:200px}
.help .btn{left:543px;top:417px}

/* placements */
.placements{top:2302px;height:558px}
.placements__title{position:absolute;width:100%;text-align:center;top:80px}
.placements .rule{position:absolute;left:578px;top:130px}
.tile{position:absolute;top:165px;width:274px;height:227px;display:flex;align-items:center;justify-content:center}
.tile span{font-size:19px;font-weight:700;color:var(--white);position:relative}
.tile--nursing{left:162px;background:linear-gradient(135deg,#7d8a95,#b9c4cc 50%,#6f7f8f)}
.tile--engineering{left:462px;background:linear-gradient(135deg,#5e5a55,#a09a8a 50%,#50575f)}
.tile--welding{left:764px;background:linear-gradient(135deg,#6b6557,#a8977a 50%,#5c5850)}
.arrow-btn{position:absolute;top:258px;width:42px;height:42px;border:1px solid var(--line);background:var(--white);display:flex;align-items:center;justify-content:center}
.placements .btn{left:547px;top:432px}

/* testimonial */
.testimonial{top:2860px;height:488px;background:var(--grey-bg)}
.testimonial__photo{left:162px;top:110px;width:324px;height:267px;background:linear-gradient(120deg,#8d8f92,#dfe2e5 45%,#6d7174)}
.quote-card{position:absolute;left:440px;top:90px;width:599px;height:307px;background:var(--white)}
.stars{position:absolute;left:103px;top:32px;display:flex;gap:4px}
.quote-card p{position:absolute;left:103px;top:64px;width:430px;font-size:13px;line-height:28px}
.quote-card .name{position:absolute;left:103px;top:245px;font-size:16px;font-weight:600;color:var(--blue)}
.quote-card .role{position:absolute;left:103px;top:268px;font-size:11px;color:#999}
.quote-card svg.qmark{position:absolute;right:36px;top:248px}

/* resources */
.resources{top:3348px;height:452px}
.res{position:absolute;top:130px;width:270px;height:234px;border:1px solid var(--line);text-align:center}
.res__icon{position:absolute;left:97px;top:-38px;width:76px;height:76px;border-radius:50%;background:var(--white);border:1px solid var(--line);display:flex;align-items:center;justify-content:center}
.res h3{font-size:15.5px;font-weight:600;margin-top:60px}
.res p{font-size:11px;line-height:23px;width:230px;margin:10px auto 0}
.res .btn{position:static;margin-top:14px;padding:10px 22px}

/* contact band */
.contact-band{top:3800px;height:450px;background:#2e2c29}
.contact-band__photo{left:590px;top:0;width:610px;height:450px;background:linear-gradient(90deg,#2e2c29,#6a5e52 30%,#b97a52 55%,#2c4f8a 85%,#1f3a68)}
.contact-band h2{position:absolute;left:162px;top:100px;color:var(--white);font-size:32px;font-weight:600}
.contact-band p{position:absolute;left:162px;top:168px;width:410px;font-size:11.5px;line-height:23px;color:var(--white)}
.contact-band .btn{left:162px;top:320px}

/* quick contact */
.quick{top:4250px;height:600px}
.quick__title{position:absolute;width:100%;text-align:center;top:92px}
.quick .rule{position:absolute;left:578px;top:143px}
.field{position:absolute;width:290px;border-bottom:1px solid var(--line);height:70px}
.field label{position:absolute;top:0;font-size:10.5px;color:#888}
.field span{position:absolute;top:28px;font-size:11px}
.field svg{position:absolute;right:2px;top:24px}
.quick .btn{left:543px;top:505px}

/* footer */
.site-footer{top:4850px;height:300px;background:var(--blue);color:var(--white)}
.footer-h{position:absolute;top:80px;font-size:14px;font-weight:600}
.footer-h::after{content:"";display:block;width:30px;height:2px;background:var(--orange);margin-top:10px}
.links{position:absolute;top:120px;left:162px;display:grid;grid-template-columns:106px 106px;row-gap:26px;font-size:12px}
.contact-list{position:absolute;left:440px;top:118px;font-size:12px;line-height:20px}
.contact-list div{display:flex;gap:12px;margin-bottom:10px}
.socials{position:absolute;left:800px;top:122px;display:flex;gap:6px}
.socials i{width:26px;height:26px;border-radius:50%;border:1.5px solid var(--white);display:block}
.footer-brand{position:absolute;left:800px;top:178px;font-size:20px;font-weight:700;display:flex;align-items:center;gap:10px}
.footer-brand b{width:24px;height:24px;background:var(--white);display:block}
.copyright{top:5150px;height:40px;background:var(--orange);color:var(--white);font-size:11px;text-align:center;line-height:40px}
</style>
</head>
<body>

<header class="site-header">
  <div class="brand"><span class="brand__dot"></span>Trellan Staffing</div>
  <nav class="nav">
    <a href="#" class="is-active">Home</a><a href="#">About</a><a href="#">Services</a><a href="#">Articles</a><a href="#">Training</a><a href="#">Contact Us</a>
  </nav>
</header>

<section class="hero">
  <div class="photo hero__bg" style="position:absolute" role="img" aria-label="Two engineers in hard hats and safety vests reviewing plans on a construction site"></div>
  <h1 class="hero__title">Recruiting and placing<br>skilled Philippine workers<br>into UK companies</h1>
  <a class="btn" href="#">Contact Us</a>
</section>

<section class="about">
  <div class="about__blob"></div>
  <div class="photo about__photo" role="img" aria-label="Two office professionals discussing work at a laptop"></div>
  <h2 class="h2 about__title">What The Business<br>is About</h2>
  <p class="about__text">We source skilled workers directly from the Philippines to work in the UK. With offices , training locations and specialist recruiters we can find the highest quality individuals to add value and resources to any UK buisness. We delivery quality based on vast experience over a number of years.</p>
  <a class="btn" href="#">Contact Us</a>
</section>

<section class="together">
  <h2 class="h2 together__title">Working Together</h2>
  <span class="rule"></span>
  <p class="together__text">We recruit the finest talent available with our dedicated 200 strong team.<br>Our centres are highlighted in <a href="#">Red Dots</a><br>on the map.</p>
  <a class="btn" href="#">Contact Us</a>
  <div class="photo together__map" role="img" aria-label="Map of the Philippines with recruitment centres marked by red dots"></div>
</section>

<section class="help">
  <div class="card" style="left:162px">
    <svg width="90" height="90" viewBox="0 0 90 90" fill="none" stroke="#0054AA" stroke-width="2.5"><circle cx="26" cy="20" r="13"/><path d="M26 12v8l6 4"/><rect x="8" y="40" width="40" height="28"/><path d="M20 68v8h20M48 56h32v20H48z"/><circle cx="66" cy="36" r="8"/><path d="M56 56c0-8 4-12 10-12s10 4 10 12"/></svg>
    <h3>What We Do</h3>
    <p>Our company has been established in the Philippines for over 20 years...</p>
  </div>
  <div class="card" style="left:470px">
    <svg width="90" height="90" viewBox="0 0 90 90" fill="none" stroke="#0054AA" stroke-width="2.5"><path d="M18 44a27 27 0 0 1 54 0"/><rect x="12" y="42" width="10" height="20" rx="4"/><rect x="68" y="42" width="10" height="20" rx="4"/><path d="M73 62c0 12-10 18-22 18"/><rect x="28" y="28" width="34" height="24" rx="6"/><circle cx="37" cy="40" r="2"/><circle cx="45" cy="40" r="2"/><circle cx="53" cy="40" r="2"/></svg>
    <h3>How We Help</h3>
    <p>We work with companies to find skilled workers that meet the UK requirements for Visas...</p>
  </div>
  <div class="card" style="left:780px">
    <svg width="90" height="90" viewBox="0 0 90 90" fill="none" stroke="#0054AA" stroke-width="2.5"><path d="M78 10C56 10 36 26 28 50l12 12c24-8 40-28 40-50z"/><circle cx="58" cy="32" r="7"/><path d="M28 50l-12 2 12-18h14M40 62l-2 12 18-12V48M22 64l-10 14M30 70l-8 10"/></svg>
    <h3>Where To Start</h3>
    <p>We need to know what your issues are and how we can understand the personnal you...</p>
  </div>
  <a class="btn" href="#">Contact Us</a>
</section>

<section class="placements">
  <h2 class="h2 placements__title">Placement We Provide In</h2>
  <span class="rule"></span>
  <div class="arrow-btn" style="left:97px"><svg width="14" height="10" viewBox="0 0 14 10" fill="none" stroke="#999" stroke-width="1.3"><path d="M13 5H1M5 1L1 5l4 4"/></svg></div>
  <div class="tile tile--nursing" role="img" aria-label="Nurses at work in a hospital ward"><span>Nursing</span></div>
  <div class="tile tile--engineering" role="img" aria-label="Engineer in a yellow hard hat"><span>Engineering</span></div>
  <div class="tile tile--welding" role="img" aria-label="Welder working in a workshop"><span>Welding</span></div>
  <div class="arrow-btn" style="left:1060px"><svg width="14" height="10" viewBox="0 0 14 10" fill="none" stroke="#999" stroke-width="1.3"><path d="M1 5h12M9 1l4 4-4 4"/></svg></div>
  <a class="btn" href="#">View All</a>
</section>

<section class="testimonial">
  <div class="photo testimonial__photo" role="img" aria-label="Engineer in a white coat and hard hat standing in a steel structure"></div>
  <div class="quote-card">
    <div class="stars">
      <svg width="96" height="18" viewBox="0 0 96 18" fill="#EE7325"><g id="st"><path d="M9 0l2.6 5.8 6.4.6-4.8 4.2 1.4 6.3L9 13.6 3.4 16.9l1.4-6.3L0 6.4l6.4-.6z"/></g><use href="#st" x="19"/><use href="#st" x="38"/><use href="#st" x="57"/><use href="#st" x="76"/></svg>
    </div>
    <p>Lorem ipsum dolor sit amet, consectetur adipiscing elit, sed do eiusmod tempor incididunt ut labore et dolore magna aliqua. Ut enim ad minim veniam, quis nostrud exercitation ullamco laboris nisi...</p>
    <div class="name">Maren Holt</div>
    <div class="role">Engineer</div>
    <svg class="qmark" width="44" height="34" viewBox="0 0 44 34" fill="#F5BC92"><path d="M0 34V18C0 8 6 1 16 0v6c-5 1-8 5-8 10h8v18zM24 34V18C24 8 30 1 40 0v6c-5 1-8 5-8 10h8v18z"/></svg>
  </div>
</section>

<section class="resources">
  <div class="res" style="left:162px">
    <div class="res__icon"><svg width="40" height="40" viewBox="0 0 40 40" fill="none" stroke="#0054AA" stroke-width="2"><rect x="8" y="6" width="22" height="30" rx="2"/><path d="M14 6V3h10v3M13 16h12M13 22h12M13 28h8"/></svg></div>
    <h3>UK Skilled Workers List</h3>
    <p>The UK government since brexit have developed a new system based on points (similar to Australia)...</p>
    <a class="btn" href="#">Read More</a>
  </div>
  <div class="res" style="left:465px">
    <div class="res__icon"><svg width="40" height="40" viewBox="0 0 40 40" fill="none" stroke="#0054AA" stroke-width="2"><rect x="12" y="4" width="20" height="30" rx="2"/><circle cx="22" cy="14" r="4"/><path d="M16 26h12M16 30h8M6 18h6M6 24h6"/></svg></div>
    <h3>Sponsor Licence</h3>
    <p>If you have areas of your business that meet the entry requirements of skilled labour your next...</p>
    <a class="btn" href="#">Read More</a>
  </div>
  <div class="res" style="left:768px">
    <div class="res__icon"><svg width="40" height="40" viewBox="0 0 40 40" fill="none" stroke="#0054AA" stroke-width="2"><circle cx="22" cy="22" r="12"/><path d="M22 14v8l5 4M8 36V22M4 36V28M12 36V18"/></svg></div>
    <h3>Recruitment Timeline</h3>
    <p>Brief us on the job profiles – this is passed on to our teams in the Philippines...</p>
    <a class="btn" href="#">Read More</a>
  </div>
</section>

<section class="contact-band">
  <div class="photo contact-band__photo" role="img" aria-label="Smiling workers in hard hats holding a laptop and a folder"></div>
  <h2>Contact Us Today</h2>
  <p>Please contact us today with your requirements, this can be care workers, chef, welders, pipe fitters, caravan cabinet makers, medical workers. The UK list of required skills is extensive and the Philippines offersenglish speaking highly qualified hard working employees. Contact us today and make that first step to a highly motivated , quality skilled workforce.</p>
  <a class="btn btn--light" href="#">Contact Us</a>
</section>

<section class="quick">
  <h2 class="h2 quick__title">Quick Contact</h2>
  <span class="rule"></span>
  <div class="field" style="left:295px;top:178px"><label>First Name</label><span>Daniel</span>
    <svg width="14" height="16" viewBox="0 0 14 16" fill="none" stroke="#999"><circle cx="7" cy="5" r="3.5"/><path d="M1 15c0-4 3-6 6-6s6 2 6 6z"/></svg></div>
  <div class="field" style="left:615px;top:178px"><label>Last Name</label><span>Ashby</span>
    <svg width="14" height="16" viewBox="0 0 14 16" fill="none" stroke="#999"><circle cx="7" cy="5" r="3.5"/><path d="M1 15c0-4 3-6 6-6s6 2 6 6z"/></svg></div>
  <div class="field" style="left:295px;top:263px"><label>Phone</label><span>123 456 7890</span>
    <svg width="16" height="16" viewBox="0 0 16 16" fill="none" stroke="#999"><path d="M3 1l3 3-2 2c1 3 3 5 6 6l2-2 3 3-2 2C7 15 1 9 1 3z"/></svg></div>
  <div class="field" style="left:615px;top:263px"><label>Email</label><span>info@danielashby.example.com</span>
    <svg width="18" height="14" viewBox="0 0 18 14" fill="none" stroke="#999"><rect x="1" y="1" width="16" height="12"/><path d="M1 1l8 7 8-7"/></svg></div>
  <div class="field" style="left:295px;top:348px;width:610px;height:100px"><label>Message</label><span>Type Your Message</span>
    <svg width="20" height="16" viewBox="0 0 20 16" fill="none" stroke="#999"><path d="M2 2h12v8H7l-3 3v-3H2zM16 5h2v8h-2v2l-3-2H9"/></svg></div>
  <a class="btn" href="#">Submit Now</a>
</section>

<footer class="site-footer">
  <div class="footer-h" style="left:162px">Quick Links</div>
  <div class="links"><span>› Home</span><span>› Articles</span><span>› About</span><span>› Training</span><span>› Services</span><span>› Contact Us</span></div>
  <div class="footer-h" style="left:440px">Contact Details</div>
  <div class="contact-list">
    <div><svg width="12" height="16" viewBox="0 0 12 16" fill="#fff"><path d="M6 0a6 6 0 0 0-6 6c0 4 6 10 6 10s6-6 6-10a6 6 0 0 0-6-6zm0 8.5A2.5 2.5 0 1 1 6 3.5a2.5 2.5 0 0 1 0 5z"/></svg><span>Orchard Row, Eastmere<br>EM4 2 United Kingdom</span></div>
    <div><svg width="14" height="14" viewBox="0 0 16 16" fill="#fff"><path d="M3 1l3 3-2 2c1 3 3 5 6 6l2-2 3 3-2 2C7 15 1 9 1 3z"/></svg><span>07700 900418</span></div>
    <div><svg width="16" height="12" viewBox="0 0 18 14" fill="none" stroke="#fff" stroke-width="1.5"><rect x="1" y="1" width="16" height="12"/><path d="M1 1l8 7 8-7"/></svg><span>sales@trellanstaffing.example.com</span></div>
  </div>
  <div class="footer-h" style="left:800px">Follow Us On:</div>
  <div class="socials"><i></i><i></i><i></i><i></i></div>
  <div class="footer-brand"><b></b>Trellan Staffing</div>
</footer>
<div class="copyright" style="position:absolute;left:0;width:1200px">© 2023 Trellan Staffing Ltd. All Rights Reserved</div>

</body>
</html>
```